Pinecrest Harbor Foundation Web Design

The design we need is for a WordPress blog that will be our content platform. We are a registered 501(c)3 non-profit that focuses on financially supporting the treatment of cancer patients that have been told they have no hope and there is nothing the conventional medical system can do for them. Through this wesbite we want to both rasie awareness about the treatment options plus, raise funds for treating patients. The two primary target audiences of the site are...

1. Terminally ill patients and their families to let them know that there is an option other then hospice and that we are hear to support that option.

2. People looking to help donate to a worthwhile cause that resonates with them.

The website is https://pinecrestharborfoundation.org/

See attached logo designs!!!

Target Market(s)

Cancer patients and their families

Industry/Entity Type

Foundation

Font styles to use
Sans Serif

Colors
ffffff
fbed22

Requirements
Must have
• I like this look of this site. It is clean, simple, helpful, soft. I like the flow of the pages.
• http://www.meadowsforcalm.org/
• I like the design and flow but NOT the color or boldness
• https://tvbn-youth.org/
• I like this style for a donation page.
• https://www.tumorstudyhub.org/we-are-tsh/join-the-cause/donations/one-time-donation
• with the addition of a Would you like your employer to match? button.
Nice to have
• White black and gold - but soft
• Even possibly grayscale like the site I like.

```html
<!DOCTYPE html>
<html lang="en">
<head>
<meta charset="utf-8">
<title>Pinecrest Harbor Foundation</title>
<link href="https://fonts.googleapis.com/css2?family=Marcellus&display=swap" rel="stylesheet">
<style>
:root{
  --gold:#e8c24c;
  --ink:#333333;
  --muted:#666666;
  --line:#d6d6d6;
  --white:#ffffff;
  --footer:#2a2a2a;
  --footer-shade:#3a3a3a;
}
*{box-sizing:border-box;margin:0;padding:0}
html,body{width:790px;height:1200px;overflow:hidden;background:var(--white)}
body{position:relative;font-family:"Marcellus",sans-serif;color:var(--ink)}
.abs{position:absolute}

.site-header{left:0;top:0;width:790px;height:78px;background:var(--white);border-top:3px solid #e6e6e6;z-index:3}
.brand-panel{left:64px;top:0;width:172px;height:136px;z-index:4}
.brand-name{left:64px;top:48px;width:172px;text-align:center;font-size:13px;line-height:15px;color:var(--ink);z-index:5;letter-spacing:.3px}
.brand-mark{left:140px;top:16px;width:20px;height:20px;background:var(--gold);z-index:5}
.main-nav{top:31px;font-size:11px;color:var(--ink);z-index:5}
.volunteer-btn{left:591px;top:25px;width:133px;height:28px;border:1.5px solid var(--gold);border-radius:2px;color:var(--gold);font-size:8.5px;letter-spacing:.3px;display:flex;align-items:center;justify-content:center;z-index:5}

.hero{left:0;top:78px;width:790px;height:316px;background:linear-gradient(90deg,#8f9a86 0%,#b4b9ae 40%,#d3c8c0 65%,#e2b9c8 85%,#c9a6b2 100%)}
.hero-title{left:40px;top:226px;width:364px;text-align:center;font-size:31px;line-height:38px;color:var(--white);text-shadow:0 1px 3px rgba(0,0,0,.25)}
.hero-dots{left:381px;top:362px;display:flex;gap:2px}
.hero-dots span{width:8px;height:8px;border-radius:50%;background:var(--white)}
.hero-dots span:first-child{background:var(--gold)}
.hero-notch{left:382px;top:393px;z-index:2}

.section-title{left:0;top:446px;width:790px;text-align:center;font-size:25px;color:var(--ink)}
.section-intro{left:140px;top:484px;width:510px;text-align:center;font-size:8.5px;line-height:20px;color:var(--muted)}

.tile{position:absolute}
.tile-child{left:65px;top:536px;width:213px;height:166px;background:linear-gradient(135deg,#9fb6c9,#e9e4de)}
.tile-hands{left:288px;top:536px;width:214px;height:344px;background:linear-gradient(160deg,#7a5a3c,#b89a7c 50%,#7f8f4a)}
.tile-volunteers{left:511px;top:536px;width:213px;height:166px;background:linear-gradient(135deg,#6f7f5a,#b79a7c 60%,#d69470)}
.tile-boxes{left:65px;top:711px;width:213px;height:169px;background:linear-gradient(135deg,#e6e2dc,#c9b08c 60%,#5fb7c9)}
.tile-thanks{left:511px;top:711px;width:213px;height:169px;background:linear-gradient(135deg,#8a6e5c,#b08e68 55%,#6c87a6)}

.social-btn{top:906px;height:29px;border:1px solid var(--line);border-radius:2px;font-size:9.5px;letter-spacing:.8px;display:flex;align-items:center;justify-content:center;gap:8px;color:var(--ink)}
.social-btn.is-primary{border:1.5px solid var(--gold);color:var(--gold)}
.btn-dot{width:7px;height:7px;background:currentColor;border-radius:1px}

.site-footer{left:0;top:994px;width:790px;height:206px;background:var(--footer)}
.footer-notch{left:376px;top:976px}
.footer-social{top:1049px;width:30px;height:30px;border-radius:50%;background:var(--white)}
.footer-nav{left:0;top:1100px;width:790px;text-align:center;font-size:11px;color:var(--white);word-spacing:2px}
.footer-nav .sep{margin:0 14px}
.copyright{left:0;top:1132px;width:790px;text-align:center;font-size:8px;color:var(--white)}
</style>
</head>
<body>

<header>
  <div class="abs site-header"></div>
  <svg class="abs brand-panel" viewBox="0 0 172 136" aria-hidden="true"><polygon points="0,0 172,0 172,78 86,136 0,78" fill="#ffffff"/></svg>
  <div class="abs brand-mark" aria-hidden="true"></div>
  <div class="abs brand-name">Pinecrest Harbor<br>Foundation</div>
  <nav>
    <span class="abs main-nav" style="left:303px">Home</span>
    <span class="abs main-nav" style="left:356px">About us</span>
    <span class="abs main-nav" style="left:421px">Donate</span>
    <span class="abs main-nav" style="left:478px">Blog</span>
    <span class="abs main-nav" style="left:523px">Contact us</span>
  </nav>
  <div class="abs volunteer-btn">BECOME A VOLUNTEER &nbsp;»</div>
</header>

<section>
  <div class="abs hero" role="img" aria-label="Smiling young patient in a pink jacket outdoors"></div>
  <h1 class="abs hero-title" style="font-weight:400">Pinecrest Harbor<br>Foundation</h1>
  <div class="abs hero-dots"><span></span><span></span><span></span></div>
  <svg class="abs hero-notch" width="26" height="20" viewBox="0 0 26 20" aria-hidden="true"><polygon points="0,0 26,0 13,20" fill="#ffffff"/></svg>
</section>

<section>
  <h2 class="abs section-title" style="font-weight:400">Donations Are Welcome !</h2>
  <p class="abs section-intro">We are a registered 501(c)3 non-profit that focuses on financially supporting the treatment of cancer patients that have been told they have no hope and there is nothing the conventional medical system can do for them.</p>

  <div class="tile tile-child" role="img" aria-label="Child in a headscarf hugging a plush toy"></div>
  <div class="tile tile-hands" role="img" aria-label="Two hands resting together in support"></div>
  <div class="tile tile-volunteers" role="img" aria-label="Volunteers packing food donations"></div>
  <div class="tile tile-boxes" role="img" aria-label="Mother and child sorting donation boxes of toys and clothes"></div>
  <div class="tile tile-thanks" role="img" aria-label="Girl holding a handwritten thank you sign"></div>

  <div class="abs social-btn is-primary" style="left:105px;width:196px"><span class="btn-dot"></span>FOLLOW US ON CIRCLEPAGE</div>
  <div class="abs social-btn" style="left:308px;width:195px"><span class="btn-dot"></span>FOLLOW US ON SNAPGRID</div>
  <div class="abs social-btn" style="left:511px;width:173px">
    <svg width="10" height="8" viewBox="0 0 10 8" aria-hidden="true"><rect x="0" y="0" width="10" height="8" fill="#333"/><polyline points="0,0 5,4.5 10,0" fill="none" stroke="#fff" stroke-width="1"/></svg>
    NEWSLETTER SIGN UP
  </div>
</section>

<footer>
  <div class="abs site-footer" role="img" aria-label="Faded portrait of a young patient on a dark background"></div>
  <svg class="abs footer-notch" width="36" height="18" viewBox="0 0 36 18" aria-hidden="true"><polygon points="0,18 18,0 36,18" fill="#2a2a2a"/></svg>
  <div class="abs footer-social" style="left:340px" aria-label="Circlepage"></div>
  <div class="abs footer-social" style="left:379px" aria-label="Chirpline"></div>
  <div class="abs footer-social" style="left:419px" aria-label="Snapgrid"></div>
  <nav class="abs footer-nav">Home<span class="sep">/</span>About us<span class="sep">/</span>Donate<span class="sep">/</span>Blog<span class="sep">/</span>Contact us</nav>
  <p class="abs copyright">© Copyright 2017 Pinecrest Harbor Foundation.All Rights Reserved</p>
</footer>

</body>
</html>
```